Concierge Healthcare Business Card Design and Logo

We need a logo and business card design for a new company called "Sound Haven". We will provide concierge audiological care, hearing aids, hearing exams, custom hearing protection etc to patients in the comfort of their homes and offices. We would like a sleek and modern design preferably with an Ear related logo.

Target Market(s)

People with hearing loss, Hunters, Musicians
My usual clientele are older individuals so usually 50+ years old

Industry/Entity Type

Health Care

Contact Information for Business Card

Celia Brandt, AuD
Audiologist
512-648-2917
soundhaven@mailvoro.com
www.soundhaven-vorel.com

Logo Text

Sound Haven

Number of Pages Required

3 page

```html
<!DOCTYPE html>
<html lang="en">
<head>
<meta charset="UTF-8">
<title>Sound Haven – Business Card</title>
<link href="https://fonts.googleapis.com/css2?family=Montserrat:wght@400;500;600;700&display=swap" rel="stylesheet">
<style>
  :root {
    --stage: #2b2b2b;
    --card-black: #050505;
    --card-white: #ffffff;
    --brand-blue: #1aa3e8;
    --ink: #1c1c1c;
    --paper-text: #ffffff;
  }
  * { margin: 0; padding: 0; box-sizing: border-box; }
  html, body {
    width: 1200px; height: 900px; overflow: hidden;
    background: var(--stage);
    font-family: "Montserrat", Arial, sans-serif;
  }
  .canvas { position: relative; width: 1200px; height: 900px; }

  .card {
    position: absolute;
    width: 640px; height: 366px;
    border-radius: 22px;
    overflow: hidden;
    background: var(--card-black);
    box-shadow: 0 10px 30px rgba(0,0,0,0.45);
  }
  .card-back { left: 180px; top: 48px; }
  .card-front { left: 380px; top: 486px; }

  /* Back side */
  .back-brand {
    position: absolute; left: 0; right: 0; top: 128px;
    display: flex; align-items: center; justify-content: center; gap: 22px;
  }
  .brand-ring {
    width: 78px; height: 78px; border-radius: 50%;
    border: 5px solid var(--brand-blue);
    flex: none;
  }
  .brand-name {
    color: var(--paper-text);
    font-weight: 600;
    font-size: 30px;
    letter-spacing: 6px;
    text-transform: uppercase;
  }
  .back-url {
    position: absolute; left: 0; right: 0; bottom: 40px;
    text-align: center;
    color: var(--paper-text);
    font-size: 17px; font-weight: 400; letter-spacing: 0.5px;
  }

  /* Front side */
  .front-shape { position: absolute; inset: 0; }
  .front-brand {
    position: absolute; left: 392px; top: 104px;
    display: flex; align-items: center; gap: 14px;
  }
  .front-brand .brand-ring { width: 52px; height: 52px; border-width: 4px; }
  .front-brand .brand-name { font-size: 19px; letter-spacing: 3px; }

  .contact-block { position: absolute; left: 48px; top: 150px; }
  .person-name {
    color: var(--brand-blue);
    font-size: 25px; font-weight: 700; line-height: 1.1;
  }
  .person-role {
    color: var(--ink);
    font-size: 15px; font-weight: 500; margin-top: 4px;
  }
  .contact-list { list-style: none; margin-top: 16px; }
  .contact-list li {
    display: flex; align-items: center; gap: 10px;
    color: var(--ink); font-size: 15px; font-weight: 500;
    line-height: 26px;
  }
  .contact-icon { width: 13px; height: 13px; flex: none; }
</style>
</head>
<body>
<div class="canvas">

  <section class="card card-back">
    <div class="back-brand">
      <span class="brand-ring"></span>
      <span class="brand-name">Sound Haven</span>
    </div>
    <p class="back-url">www.soundhaven-vorel.com</p>
  </section>

  <section class="card card-front">
    <svg class="front-shape" width="640" height="366" viewBox="0 0 640 366">
      <rect width="640" height="366" fill="var(--card-black)"/>
      <circle cx="-40" cy="200" r="412" fill="none" stroke="var(--brand-blue)" stroke-width="5"/>
      <circle cx="-40" cy="200" r="400" fill="var(--card-white)"/>
    </svg>

    <div class="front-brand">
      <span class="brand-ring"></span>
      <span class="brand-name">Sound Haven</span>
    </div>

    <div class="contact-block">
      <h1 class="person-name">Celia Brandt, AuD</h1>
      <p class="person-role">Audiologist</p>
      <ul class="contact-list">
        <li>
          <svg class="contact-icon" viewBox="0 0 24 24"><path fill="var(--brand-blue)" d="M6.6 10.8a15.2 15.2 0 0 0 6.6 6.6l2.2-2.2a1 1 0 0 1 1-.25 11.4 11.4 0 0 0 3.6.57 1 1 0 0 1 1 1V20a1 1 0 0 1-1 1A17 17 0 0 1 3 4a1 1 0 0 1 1-1h3.5a1 1 0 0 1 1 1c0 1.25.2 2.45.57 3.57a1 1 0 0 1-.25 1z"/></svg>
          512-648-2917
        </li>
        <li>
          <svg class="contact-icon" viewBox="0 0 24 24"><rect x="2" y="5" width="20" height="14" rx="2" fill="none" stroke="var(--brand-blue)" stroke-width="2.4"/><path d="M3 6l9 7 9-7" fill="none" stroke="var(--brand-blue)" stroke-width="2.4"/></svg>
          soundhaven@mailvoro.com
        </li>
        <li>
          <svg class="contact-icon" viewBox="0 0 24 24"><g fill="none" stroke="var(--brand-blue)" stroke-width="2"><circle cx="12" cy="12" r="10"/><ellipse cx="12" cy="12" rx="4.5" ry="10"/><path d="M2 12h20M4 7h16M4 17h16"/></g></svg>
          www.soundhaven-vorel.com
        </li>
      </ul>
    </div>
  </section>

</div>
</body>
</html>
```